Marlo Tidecrest SUP Boards

We are a 100% owned and operated Australian Stand Up Paddle Board company, specialising in online sales of Stand Up Paddle Board packages.

We want our website to have an ocean, sunset, beach warm feel.

We sell 4 packages and need to be able to edit content and upload a number of photos of each package for sale.

Customers will be able to email us to receive quotes on freight costs and then pay via CoinLark only. We will have a Chatterbox page and Swapnest adds that need to be linked to the website also.

Target Market(s)

Surfers and Stand up paddle boarders

Industry/Entity Type

It Company

Number of Pages Required

3 page

Requirements
Must have
• Link to CoinLark for payment
• Link to Chatterbox page
• Three tabs- Welcome page, SUP Boards and a Contact us page

```html
<!DOCTYPE html>
<html lang="en">
<head>
<meta charset="utf-8">
<title>Marlo Tidecrest SUP Boards</title>
<link href="https://fonts.googleapis.com/css2?family=Roboto:wght@300;400;500;700&family=Open+Sans:wght@400;600&display=swap" rel="stylesheet">
<style>
:root{
  --orange:#e8842a;
  --orange-band:#ef9a1c;
  --orange-light:#f09a45;
  --slate:#454e5c;
  --purple:#b03fb6;
  --magenta:#a8309f;
  --ink:#333a42;
  --muted:#6b6f75;
  --line:#e6e8eb;
  --panel:#f7f8fa;
  --footer:#1e2a36;
  --footer-deep:#16212b;
  --footer-field:#151e27;
  --footer-text:#8d97a2;
  --blue:#14a6d3;
  --amber:#f08a1d;
  --green:#5cc22d;
  --red:#e8470c;
  --link-blue:#2a7fb8;
}
*{margin:0;padding:0;box-sizing:border-box}
html,body{width:1200px;height:2416px;overflow:hidden}
body{font-family:"Roboto",sans-serif;color:var(--ink);background:#fff;position:relative}
.abs{position:absolute}

/* header */
.site-header{position:absolute;left:0;top:0;width:1200px;height:113px;background:var(--orange)}
.brand{position:absolute;left:70px;top:0;width:330px;height:113px;
  background:radial-gradient(ellipse 60% 70% at 50% 50%,#ffd21a 0%,#f7b51c 55%,rgba(232,132,42,0) 100%)}
.brand-name{position:absolute;left:36px;top:38px;font:700 30px/1 "Roboto",sans-serif;color:#1a1a1a;white-space:nowrap}
.main-nav{position:absolute;top:50px;left:0;width:1200px}
.main-nav a{position:absolute;font:400 14px/1 "Roboto",sans-serif;color:#fff;text-decoration:none;letter-spacing:.3px}

/* hero */
.hero{position:absolute;left:0;top:113px;width:1200px;height:544px;
  background:linear-gradient(180deg,#8a8780 0%,#a9a59b 30%,#c8c2b4 52%,#8f8a80 70%,#b3ada0 100%)}
.hero-caption-title{position:absolute;left:697px;top:322px;width:311px;height:50px;background:var(--orange);
  color:#fff;font:500 27px/50px "Roboto",sans-serif;padding-left:14px}
.hero-caption-text{position:absolute;left:697px;top:380px;width:403px;height:60px;background:rgba(60,60,60,.75);
  color:#fff;font:400 13px/20px "Open Sans",sans-serif;padding:8px 12px}
.hero-arrow{position:absolute;top:356px;width:34px;height:34px;border-radius:50%;background:rgba(40,40,40,.55)}
.hero-arrow svg{position:absolute;left:11px;top:10px}

/* booking band */
.booking-band{position:absolute;left:0;top:657px;width:1200px;height:158px;background:var(--orange)}
.booking-box{position:absolute;left:301px;top:36px;width:597px;height:82px;border:1px solid #f3a25f;background:var(--orange-light);border-radius:3px}
.booking-box p{position:absolute;left:37px;top:30px;color:#fff;font:400 18px/1 "Roboto",sans-serif}
.btn-white{position:absolute;left:410px;top:23px;width:136px;height:36px;background:#fff;color:var(--link-blue);
  font:500 12px/36px "Roboto",sans-serif;text-align:center;border-radius:2px}

/* packages */
.package{position:absolute;top:854px;width:230px;height:444px;background:var(--panel);border:1px solid var(--line)}
.package-head{height:64px;background:var(--slate);color:#fff;font:400 22px/64px "Roboto",sans-serif;text-align:center;margin:-1px -1px 0}
.package-price{height:58px;border-bottom:1px solid var(--line);font:400 17px/58px "Roboto",sans-serif;text-align:center;color:#4b525b;background:#f3f4f6}
.package ul{list-style:none;background:#fff;margin:0 1px}
.package li{height:39px;border-bottom:1px solid var(--line);font:400 12.5px/39px "Open Sans",sans-serif;text-align:center;color:#777}
.btn-purple{position:absolute;left:42px;top:384px;width:145px;height:34px;background:var(--purple);color:#fff;
  font:600 14px/34px "Open Sans",sans-serif;text-align:center;border-radius:2px}

.wave-divider{position:absolute;left:0;top:1348px;width:1200px;height:10px;
  background:radial-gradient(circle at 6px -2px,transparent 6px,#e3e3e3 6px,#e3e3e3 7.5px,transparent 7.5px) 0 0/12px 10px repeat-x}

/* welcome */
.welcome-title{position:absolute;left:0;top:1396px;width:1200px;text-align:center;font:400 32px/1.2 "Roboto",sans-serif;color:#333}
.welcome-title span{color:var(--magenta)}
.welcome-text{position:absolute;left:160px;top:1450px;width:880px;text-align:center;font:400 12px/20px "Open Sans",sans-serif;color:#555}

.feature{position:absolute;top:1545px;width:235px;height:290px;background:#fff;box-shadow:0 4px 8px rgba(0,0,0,.12);border:1px solid #eee}
.feature-head{height:40px;color:#fff;font:400 14px/40px "Roboto",sans-serif;text-align:center;margin:-1px -1px 0}
.feature-photo{position:absolute;left:12px;top:52px;width:210px;height:146px}
.feature p{position:absolute;left:10px;top:211px;width:215px;text-align:center;font:400 11.5px/20px "Open Sans",sans-serif;color:#444}

/* social band */
.social-band{position:absolute;left:0;top:1890px;width:1200px;height:115px;background:var(--orange-band)}
.social-band .dot{position:absolute;left:313px;top:37px;width:24px;height:24px;border-radius:50%;background:#fff}
.social-band .handle{position:absolute;left:364px;top:41px;font:400 13px/1 "Open Sans",sans-serif;color:#fff}
.social-band .tweet{position:absolute;left:477px;top:41px;font:400 14px/1 "Open Sans",sans-serif;color:#2a5d1c}
.social-band .time{position:absolute;left:536px;top:70px;font:400 10px/1 "Open Sans",sans-serif;color:#fff}
.zigzag{position:absolute;left:0;top:1998px}

/* footer */
.site-footer{position:absolute;left:0;top:2005px;width:1200px;height:333px;background:var(--footer)}
.footer-title{position:absolute;top:46px;font:400 14px/1 "Roboto",sans-serif;color:#d8dde2;letter-spacing:.2px}
.footer-note{position:absolute;left:97px;top:82px;width:260px;font:400 12px/20px "Open Sans",sans-serif;color:var(--footer-text)}
.field{position:absolute;left:97px;width:258px;height:40px;background:var(--footer-field);color:#6e7883;font:400 12px/40px "Open Sans",sans-serif;padding-left:14px}
.btn-submit{position:absolute;left:97px;top:258px;width:258px;height:44px;background:var(--footer-field);color:#fff;font:500 17px/44px "Roboto",sans-serif;text-align:center}
.thumb{position:absolute;width:112px;height:106px}
.news-item{position:absolute;left:847px;width:270px;height:95px}
.news-date{position:absolute;left:0;top:0;width:72px;height:80px;background:#111820;color:#fff;text-align:center;font:400 11px/14px "Open Sans",sans-serif;padding-top:14px}
.news-date small{display:block;font-size:9px}
.news-head{position:absolute;left:87px;top:0;font:400 12.5px/1 "Open Sans",sans-serif;color:#fff}
.news-body{position:absolute;left:87px;top:20px;width:180px;font:400 12px/20px "Open Sans",sans-serif;color:var(--footer-text)}
.news-more{position:absolute;left:87px;top:72px;font:400 12px/1 "Open Sans",sans-serif;color:var(--footer-text)}

.bottom-bar{position:absolute;left:0;top:2338px;width:1200px;height:78px;background:var(--footer-deep)}
.copyright{position:absolute;left:97px;top:33px;font:400 12px/1 "Open Sans",sans-serif;color:var(--footer-text)}
.social-icons{position:absolute;left:888px;top:33px}
.social-icons span{position:absolute;top:0;width:14px;height:14px;border-radius:50%;background:#b7c1cb}
.social-icons span.first{background:var(--blue)}
</style>
</head>
<body>

<header class="site-header">
  <div class="brand"><div class="brand-name">Marlo Tidecrest</div></div>
  <nav class="main-nav">
    <a style="left:541px">HOME</a>
    <a style="left:625px">ABOUT US</a>
    <a style="left:738px">PRICES &amp; PACKAGES</a>
    <a style="left:923px">SERVICES</a>
    <a style="left:1033px">CONTACT</a>
  </nav>
</header>

<section class="hero" role="img" aria-label="Surfer carrying a board along the shoreline at dusk">
  <div class="hero-arrow" style="left:33px"><svg width="12" height="14" viewBox="0 0 12 14"><path d="M9 1 3 7l6 6" stroke="#fff" stroke-width="2" fill="none"/></svg></div>
  <div class="hero-arrow" style="left:1130px"><svg width="12" height="14" viewBox="0 0 12 14"><path d="m3 1 6 6-6 6" stroke="#fff" stroke-width="2" fill="none"/></svg></div>
</section>
<div class="hero-caption-title">MARLO TIDECREST</div>
<div class="hero-caption-text">Sed ut perspiciatis unde omnis iste natus error sit voluptatem accusantium doloremque laudantium, totam rem aperiam.</div>

<section class="booking-band">
  <div class="booking-box">
    <p>Donec sollicitudin molestie malesuada oulla</p>
    <div class="btn-white">BOOKING NOW</div>
  </div>
</section>

<section class="packages">
  <div class="package" style="left:99px"><div class="package-head">Package</div><div class="package-price">$5.01/ Month</div>
    <ul><li>Lorem ipsum</li><li>Dolor sit amet, consect</li><li>Adipiscing elit</li><li>Proin commodo turpis</li><li>lacus pulvinarvel</li><li>Prnare nisi pretium.</li></ul>
    <div class="btn-purple">Booking now</div></div>
  <div class="package" style="left:356px"><div class="package-head">Package</div><div class="package-price">$5.01/ Month</div>
    <ul><li>Lorem ipsum</li><li>Dolor sit amet, consect</li><li>Adipiscing elit</li><li>Proin commodo turpis</li><li>lacus pulvinarvel</li><li>Prnare nisi pretium.</li></ul>
    <div class="btn-purple">Booking now</div></div>
  <div class="package" style="left:613px"><div class="package-head">Package</div><div class="package-price">$5.01/ Month</div>
    <ul><li>Lorem ipsum</li><li>Dolor sit amet, consect</li><li>Adipiscing elit</li><li>Proin commodo turpis</li><li>lacus pulvinarvel</li><li>Prnare nisi pretium.</li></ul>
    <div class="btn-purple">Booking now</div></div>
  <div class="package" style="left:870px"><div class="package-head">Package</div><div class="package-price">$5.01/ Month</div>
    <ul><li>Lorem ipsum</li><li>Dolor sit amet, consect</li><li>Adipiscing elit</li><li>Proin commodo turpis</li><li>lacus pulvinarvel</li><li>Prnare nisi pretium.</li></ul>
    <div class="btn-purple">Booking now</div></div>
</section>

<div class="wave-divider"></div>

<h1 class="welcome-title">Welcome To <span>MARLO TIDECREST</span></h1>
<p class="welcome-text">Lorem ipsum dolor sit amet, consectetur adipiscing elit, sed do eiusmod tempor incididunt ut labore et dolore magna aliqua. Ut enim ad minim veniam, quis nostrud exercitation ullamco laboris nisi ut aliquip ex ea commodo consequat. Duis aute irure dolor in reprehenderit in voluptate velit esse cillum dolore eu fugiat nulla pariatur. Excepteur sint occaecat cupidatat non proident, sunt in culpa qui officia deserunt mollit anim id est laborum</p>

<section class="features">
  <article class="feature" style="left:99px"><div class="feature-head" style="background:var(--blue)">SED UT PERSPICIATIS UNDE</div>
    <div class="feature-photo" role="img" aria-label="Windsurfer riding across blue water" style="background:linear-gradient(180deg,#9cc4e4,#2d6ea6)"></div>
    <p>Lorem ipsum dolor sit amet, consectetur adipiscing elit, sed do eiusmod tempor incididunt ut labore et dolore</p></article>
  <article class="feature" style="left:356px"><div class="feature-head" style="background:var(--amber)">SED UT PERSPICIATIS UNDE</div>
    <div class="feature-photo" role="img" aria-label="Two surfers holding boards on a sunny beach" style="background:linear-gradient(180deg,#cfe3ee,#d9c7a8)"></div>
    <p>Lorem ipsum dolor sit amet, consectetur adipiscing elit, sed do eiusmod tempor incididunt ut labore et dolore</p></article>
  <article class="feature" style="left:613px"><div class="feature-head" style="background:var(--green)">SED UT PERSPICIATIS UNDE</div>
    <div class="feature-photo" role="img" aria-label="Kitesurfer jumping over a wave" style="background:linear-gradient(180deg,#a8c6de,#1f5c8f)"></div>
    <p>Lorem ipsum dolor sit amet, consectetur adipiscing elit, sed do eiusmod tempor incididunt ut labore et dolore</p></article>
  <article class="feature" style="left:870px"><div class="feature-head" style="background:var(--red)">SED UT PERSPICIATIS UNDE</div>
    <div class="feature-photo" role="img" aria-label="Group of surfers walking toward the sea" style="background:linear-gradient(180deg,#d8d8d6,#8e8e8a)"></div>
    <p>Lorem ipsum dolor sit amet, consectetur adipiscing elit, sed do eiusmod tempor incididunt ut labore et dolore</p></article>
</section>

<section class="social-band">
  <span class="dot"></span>
  <span class="handle">@Marlo Tidecrest</span>
  <span class="tweet">Donec sollicitudin molestie malesuada. Nulla quis lorem ut libero</span>
  <span class="time">about 13 hours,12 minutes ago</span>
</section>
<svg class="zigzag" width="1200" height="10" viewBox="0 0 1200 10" preserveAspectRatio="none">
  <defs><pattern id="zz" width="12" height="10" patternUnits="userSpaceOnUse"><path d="M0 0 6 8 12 0Z" fill="#ef9a1c"/></pattern></defs>
  <rect width="1200" height="10" fill="#1e2a36"/><rect width="1200" height="10" fill="url(#zz)"/>
</svg>

<footer class="site-footer">
  <h3 class="footer-title" style="left:97px">NEWSLETTER SIGNUP</h3>
  <p class="footer-note">Sign up for our newsletter and get the latest news.</p>
  <div class="field" style="top:140px">Name</div>
  <div class="field" style="top:200px">E - Mail</div>
  <div class="btn-submit">Submit Now</div>

  <h3 class="footer-title" style="left:436px">SNAPREEL PHOTOSTREAM</h3>
  <div class="thumb" role="img" aria-label="Surfer with board" style="left:436px;top:86px;background:linear-gradient(#b9dcef,#e8eef2)"></div>
  <div class="thumb" role="img" aria-label="Surfer in the waves" style="left:552px;top:86px;background:linear-gradient(#9fc2d9,#4e7a93)"></div>
  <div class="thumb" role="img" aria-label="Surfers on the beach" style="left:668px;top:86px;background:linear-gradient(#d4d6d8,#7d8186)"></div>
  <div class="thumb" role="img" aria-label="Paddler at the shoreline" style="left:436px;top:196px;background:linear-gradient(#c9c3b3,#6f6c66)"></div>
  <div class="thumb" role="img" aria-label="Surfer paddling out" style="left:552px;top:196px;background:linear-gradient(#8fc3d6,#2f6f86)"></div>
  <div class="thumb" role="img" aria-label="Windsurfer on open water" style="left:668px;top:196px;background:linear-gradient(#b6d3ea,#2c62a0)"></div>

  <h3 class="footer-title" style="left:847px">LATEST NEWS</h3>
  <div class="news-item" style="top:86px">
    <div class="news-date">12<small>JAN</small>2015</div>
    <div class="news-head">Morbi rhoncus, ante ege</div>
    <div class="news-body">Morbi rhoncus, ante eget fer-mentum aucto...</div>
    <div class="news-more">View more »</div>
  </div>
  <div class="news-item" style="top:197px">
    <div class="news-date">12<small>JAN</small>2015</div>
    <div class="news-head">Morbi rhoncus, ante ege</div>
    <div class="news-body">Morbi rhoncus, ante eget fer-mentum aucto...</div>
    <div class="news-more">View more »</div>
  </div>
</footer>

<div class="bottom-bar">
  <p class="copyright">© Copyright 2015 Marlo Tidecrest.All Rights Reserved.</p>
  <div class="social-icons">
    <span class="first" style="left:0"></span>
    <span style="left:32px"></span>
    <span style="left:64px"></span>
    <span style="left:96px"></span>
    <span style="left:128px"></span>
    <span style="left:160px"></span>
    <span style="left:192px"></span>
  </div>
</div>

</body>
</html>
```